Wordpress Web Design & Coding for velcorahealth.ca

We need a website for a new investment company that is visually grabbing and vibrant. We would like to see a web page that displays trust, growth and confidence. Needs to be responsive and mobile friendly for all browsers and coded for both Android & IOS.

Open to the number of pages and menu items. I selected 4 but if you feel the layout would work better with less I am open to this. Need to sell the people (management team/related businesses) and then show where the invested money will be going (upcoming projects).

Company Info:

Vel Cora is an investment company put together by a group of seasoned business professionals who have come together to combine decades of success in the real estate development, management, financing and medical services. The company will be a full service company offering turn key solutions for medical professionals.

Vel-Cora will focus on providing a full range of services via a group of distinct companies to deliver newly emerging needs of the medical community. The end goal will be to create complete solutions for individuals in the medical community. Our group has experience and success with the conceptualization, construction and financing of medical and dental clinic spaces. Vel-Cora Solutions will be established to accommodate all areas of the development and creation of clinics for medical professionals from building construction to equipment financing and administrations.

You can mention these companies and take photos from their websites. You can also use stock photos.

Our construction partner:
https://318bld.com/projects/

Our equipment leasing partner:
https://www.norvixa.com/

Our Management Team and medical partners

Gil Parish
https://www.ourfirmstance.ca/

Dietmar Vellasquin
https://www.gshdentalservices.com/about-us

PROPOSED PROJECTS (see attachment for details)
Pinegrove Business Park
Holtmere Business Park
Mt. Corwin Ridge Professional

Target Market(s)

Investors

Industry/Entity Type

Investment

Coding

Coded - Design and coding required

Number of Pages Required

4 page

Font styles to use
Sans Serif

Requirements
Must have
• Wordpress – must be both desktop and mobile friendly with fast page load speed
Ability to edit after ourselves in Wordpress
Attractive home page with logo etc.
Logo colours are: for the blue the pantone color is #0355a3
and for the green is #8cc63f

Sections, about us, what we do/services we provide, contact us

```html
<!DOCTYPE html>
<html lang="en">
<head>
<meta charset="utf-8">
<title>Vel-Cora Solutions</title>
<link rel="stylesheet" href="https://fonts.googleapis.com/css2?family=Roboto:wght@300;400;500;700&family=PT+Serif&display=swap">
<style>
:root{
  --blue:#0355a3;
  --blue-deep:#0b4a96;
  --blue-soft:#2f6fbd;
  --green:#8cc63f;
  --grey-panel:#f3f3f3;
  --text:#4a4a4a;
  --muted:#8a8a8a;
  --footer:#2b2b2b;
  --footer-base:#232323;
  --page:#e6e6e6;
}
*{box-sizing:border-box;margin:0;padding:0}
html,body{width:1200px;height:2678px;overflow:hidden}
body{background:var(--page);font-family:"Roboto",sans-serif;color:var(--text)}
.site{position:absolute;left:113px;top:0;width:973px;height:2678px;background:#fff;overflow:hidden}

/* header */
.header{height:71px;display:flex;align-items:center;padding:0 40px 0 66px;position:relative}
.brand{display:flex;align-items:center;gap:7px;font-weight:700;font-size:17px;color:var(--blue);letter-spacing:.5px}
.brand-square{width:11px;height:11px;background:var(--green)}
.nav{display:flex;gap:26px;margin-left:92px;font-size:9px;color:#555;font-weight:500;align-items:center}
.nav a{text-decoration:none;color:inherit}
.nav .active{border:1.5px solid var(--green);color:var(--green);padding:8px 12px}
.callout{margin-left:auto;display:flex;align-items:center;gap:8px}
.callout-icon{width:34px;height:34px;border-radius:50%;background:var(--blue);display:flex;align-items:center;justify-content:center}
.callout-num{color:var(--green);font-weight:500;font-size:15px;line-height:1.1}
.callout-note{color:var(--muted);font-size:9px}

/* hero */
.hero{height:411px;display:flex;position:relative}
.hero-photo{width:488px;height:100%;background:linear-gradient(160deg,#5d8fcf 0%,#2e6db8 45%,#174f98 100%)}
.hero-panel{flex:1;background:var(--grey-panel);padding:58px 40px 0 35px}
.hero-title{font-weight:300;font-size:34px;line-height:42px;color:var(--blue)}
.hero-title span{display:block;color:var(--green)}
.hero-copy{margin-top:42px;font-size:10px;line-height:19.5px;width:412px;color:#555}
.btn{display:inline-flex;align-items:center;justify-content:center;background:var(--green);color:#fff;font-weight:500;font-size:11px;height:40px;border-radius:2px}
.hero .btn{margin-top:24px;width:113px}
.hero-wave{position:absolute;left:0;bottom:0;width:100%;height:40px}

/* section heading */
.heading{font-weight:300;font-size:24px;letter-spacing:.4px}
.rule{height:4px;margin-top:10px;background:repeating-linear-gradient(90deg,var(--green) 0 2px,transparent 2px 4px);opacity:.6}

/* about */
.about{height:397px;position:relative;padding:42px 0 0 113px}
.about .heading{color:var(--blue)}
.about .rule{width:123px}
.about-copy{margin-top:16px;width:350px;font-size:10px;line-height:19.5px;color:#555}
.about .btn{margin-top:27px;width:258px}
.about-mark{position:absolute;left:585px;top:150px;display:flex;align-items:center;gap:14px;font-size:52px;font-weight:700;color:var(--blue)}
.about-mark i{width:30px;height:30px;background:var(--green);display:block}

/* services */
.services{height:524px;position:relative;text-align:center;color:#fff}
.services-bg{position:absolute;inset:0;background:linear-gradient(135deg,#3d7cc7 0%,#1b5ea9 50%,#0f4c97 100%)}
.services-inner{position:relative;padding-top:42px}
.services .rule{width:123px;margin:10px auto 0;background:repeating-linear-gradient(90deg,#9fbbe0 0 2px,transparent 2px 4px)}
.services-lead{margin:26px auto 0;width:760px;font-weight:300;font-size:17px;line-height:26px}
.cards{display:flex;gap:15px;justify-content:center;margin-top:24px}
.card{width:254px;height:223px;background:#fff;padding:22px 22px 0}
.card-icon{width:58px;height:58px;margin:0 auto;border:2px solid var(--green);border-radius:6px;background:#eef7e3}
.card-title{margin-top:14px;color:var(--blue);font-weight:500;font-size:14px;line-height:20px}
.card-text{margin-top:12px;color:var(--muted);font-size:9.5px;line-height:19px}
.services .btn{margin-top:29px;width:191px}

/* projects */
.projects{height:541px;position:relative}
.projects .heading{color:var(--blue);text-align:center;padding-top:56px}
.projects .rule{width:283px;margin:12px auto 0}
.project-photo{position:absolute;left:83px;top:130px;width:405px;height:324px;background:linear-gradient(180deg,#6f8fb3 0%,#a9bccf 45%,#d7dadb 62%,#5c5f63 100%)}
.project-info{position:absolute;left:532px;top:170px;width:360px}
.project-title{font-weight:300;font-size:19px;color:#555}
.project-sub{margin-top:4px;font-size:9px;color:var(--muted)}
.project-copy{margin-top:20px;font-family:"PT Serif",serif;font-size:10.5px;line-height:17.5px;color:#777}
.arrow{position:absolute;width:42px;height:42px;background:var(--blue-soft);display:flex;align-items:center;justify-content:center}
.arrow-next{left:532px;top:414px}
.arrow-prev{left:488px;top:456px}

/* callback */
.callback{height:482px;position:relative;text-align:center;color:#fff}
.callback-bg{position:absolute;inset:0;background:linear-gradient(150deg,#2f6fbd 0%,#1b5ea9 55%,#3f79bf 100%)}
.callback-inner{position:relative;padding-top:55px}
.callback .rule{width:123px;margin:10px auto 0;background:repeating-linear-gradient(90deg,#9fbbe0 0 2px,transparent 2px 4px)}
.form{position:absolute;left:235px;top:115px;width:503px;height:324px;background:#fff;border-radius:3px;padding:35px 35px 0;text-align:left}
.field{height:33px;border:1px solid #d8d8d8;margin-bottom:8px;font-size:9px;color:#888;padding:10px 12px}
.field-msg{height:85px}
.form .btn{width:100%;height:32px;margin-top:2px;font-size:10px}

/* footer */
.footer{height:194px;background:var(--footer);color:#fff;position:relative}
.footer-brand{position:absolute;left:125px;top:40px;text-align:center}
.footer-brand .brand{font-size:17px;color:var(--blue)}
.footer-sub{font-size:9px;color:var(--green);letter-spacing:1px;margin-top:2px}
.socials{display:flex;gap:5px;justify-content:center;margin-top:12px}
.socials i{width:20px;height:20px;display:block;background:var(--blue-soft);border-radius:2px}
.socials i:nth-child(2){background:#4a90d9}
.socials i:nth-child(3){background:#c8392f}
.col{position:absolute;top:38px}
.col h4{font-weight:300;font-size:15px}
.col ul{list-style:none;margin-top:22px}
.col li{font-size:9.5px;line-height:22px;color:#e6e6e6;display:flex;gap:8px}
.col li b{color:var(--green);font-weight:400}
.col-partners{left:292px}
.col-resources{left:493px}
.col-contacts{left:696px;width:200px}
.copyright{height:58px;background:var(--footer-base);border-top:1px solid #3a3a3a;display:flex;align-items:center;justify-content:center;font-size:9.5px;color:#ddd}
</style>
</head>
<body>
<div class="site">

  <header class="header">
    <div class="brand"><span class="brand-square"></span>VEL-CORA</div>
    <nav class="nav">
      <a class="active" href="#">Home</a>
      <a href="#">About Us</a>
      <a href="#">What We Do</a>
      <a href="#">Our Projects</a>
      <a href="#">Contact Us</a>
    </nav>
    <div class="callout">
      <div class="callout-icon">
        <svg width="16" height="16" viewBox="0 0 24 24"><path fill="#fff" d="M6.6 10.8c1.4 2.8 3.8 5.1 6.6 6.6l2.2-2.2c.3-.3.7-.4 1-.2 1.1.4 2.3.6 3.6.6.6 0 1 .4 1 1V20c0 .6-.4 1-1 1C10.6 21 3 13.4 3 4c0-.6.4-1 1-1h3.5c.6 0 1 .4 1 1 0 1.3.2 2.5.6 3.6.1.3 0 .7-.2 1z"/></svg>
      </div>
      <div>
        <div class="callout-num">318-642-7710</div>
        <div class="callout-note">Call us now for more info</div>
      </div>
    </div>
  </header>

  <section class="hero">
    <div class="hero-photo" role="img" aria-label="Modern two-storey commercial building under a blue tint"></div>
    <div class="hero-panel">
      <h1 class="hero-title">Invest in<span>Your Trusted Company</span></h1>
      <p class="hero-copy">Vel Cora is an investment company put together by a group of seasoned business professionals who have come together to combine decades of success in the real estate development, management, financing and medical services. The company will be a full service company offering turn key solutions for medical professionals.</p>
      <a class="btn" href="#">More Info</a>
    </div>
    <svg class="hero-wave" viewBox="0 0 973 40" preserveAspectRatio="none"><path d="M0 22 C300 8 650 36 973 14 L973 40 L0 40Z" fill="#fff" opacity=".35"/><path d="M0 32 C350 20 640 40 973 28 L973 40 L0 40Z" fill="#fff"/></svg>
  </section>

  <section class="about">
    <h2 class="heading">ABOUT US</h2>
    <div class="rule"></div>
    <p class="about-copy">Vel-Cora will focus on providing a full range of services via a group of distinct companies to deliver newly emerging needs of the medical community. The end goal will be to create complete solutions for individuals in the medical community. Our group has experience and success with the conceptualization, construction and financing of medical and dental clinic spaces. Vel-Cora Solutions will be established to accommodate all areas of the development and creation of clinics for medical professionals from building construction to equipment financing and administrations.</p>
    <a class="btn" href="#">Our Management Team &amp; Partners</a>
    <div class="about-mark"><i></i>VEL-CORA</div>
  </section>

  <section class="services">
    <div class="services-bg" role="img" aria-label="Glass office building facade under a blue tint"></div>
    <div class="services-inner">
      <h2 class="heading">WHAT WE DO</h2>
      <div class="rule"></div>
      <p class="services-lead">Vel-Cora Solutions established to accommodate all areas of the development and creation of clinics for medical professionals</p>
      <div class="cards">
        <div class="card">
          <div class="card-icon" role="img" aria-label="Construction crane icon"></div>
          <h3 class="card-title">Medical Building<br>Construction</h3>
          <p class="card-text">Lorem ipsum dolor sit amet, consectetur adipiscing elit. Ut elit tellus, luctus nec ullamcorper mattis, pulvinar dapibus leo.</p>
        </div>
        <div class="card">
          <div class="card-icon" role="img" aria-label="Banknotes and coins icon"></div>
          <h3 class="card-title">Equipment<br>Financing</h3>
          <p class="card-text">Lorem ipsum dolor sit amet, consectetur adipiscing elit. Ut elit tellus, luctus nec ullamcorper mattis, pulvinar dapibus leo.</p>
        </div>
        <div class="card">
          <div class="card-icon" role="img" aria-label="Planning board icon"></div>
          <h3 class="card-title">Construction<br>Administrations</h3>
          <p class="card-text">Lorem ipsum dolor sit amet, consectetur adipiscing elit. Ut elit tellus, luctus nec ullamcorper mattis, pulvinar dapibus leo.</p>
        </div>
      </div>
      <a class="btn" href="#">Our Upcoming Projects</a>
    </div>
  </section>

  <section class="projects">
    <h2 class="heading">UPCOMING PROJECTS</h2>
    <div class="rule"></div>
    <div class="project-photo" role="img" aria-label="Light industrial building with parking lot under a cloudy sky"></div>
    <div class="project-info">
      <h3 class="project-title">Pinegrove Business Park</h3>
      <p class="project-sub">Office and light Industrial Building Project</p>
      <p class="project-copy">Lorem ipsum dolor sit amet, consectetur adipiscing elit, sed do eiusmod tempor incididunt ut labore et dolore magna aliqua. Ut enim ad minim veniam, quis nostrud exercitation ullamco laboris nisi ut aliquip ex ea commodo consequat. Duis aute irure dolor in reprehenderit in voluptate velit esse cillum dolore eu fugiat nulla pariatur.</p>
    </div>
    <a class="arrow arrow-next" href="#" aria-label="Next project"><svg width="12" height="12" viewBox="0 0 12 12"><path d="M4 2l4 4-4 4" stroke="#fff" stroke-width="1.6" fill="none"/></svg></a>
    <a class="arrow arrow-prev" href="#" aria-label="Previous project"><svg width="12" height="12" viewBox="0 0 12 12"><path d="M8 2L4 6l4 4" stroke="#fff" stroke-width="1.6" fill="none"/></svg></a>
  </section>

  <section class="callback">
    <div class="callback-bg" role="img" aria-label="Professional building exterior under a blue tint"></div>
    <div class="callback-inner">
      <h2 class="heading">REQUEST A CALL BACK</h2>
      <div class="rule"></div>
    </div>
    <form class="form">
      <div class="field">Name</div>
      <div class="field">Phone</div>
      <div class="field">Email</div>
      <div class="field field-msg">Message</div>
      <div class="btn">SEND</div>
    </form>
  </section>

  <footer class="footer">
    <div class="footer-brand">
      <div class="brand"><span class="brand-square"></span>VEL-CORA</div>
      <div class="footer-sub">SOLUTIONS</div>
      <div class="socials" aria-label="Social links"><i></i><i></i><i></i></div>
    </div>
    <div class="col col-partners">
      <h4>PARTNERS</h4>
      <ul><li>318 Developments</li><li>Norvixa Equipment Leasing</li><li>Firm Stance</li><li>GSH Dental Services</li></ul>
    </div>
    <div class="col col-resources">
      <h4>RESOURCES</h4>
      <ul><li>Home</li><li>About Us</li><li>Projects</li><li>Contact Us</li></ul>
    </div>
    <div class="col col-contacts">
      <h4>CONTACTS</h4>
      <ul>
        <li><b>&#9679;</b>Lorem ipsum dolor sit amet,<br>consectetur adipiscing elit</li>
        <li><b>&#9742;</b>318-640-2215</li>
        <li><b>&#9993;</b>info@velcorahealth.ca</li>
      </ul>
    </div>
  </footer>
  <div class="copyright">Copyright © 2020 VEL-CORA Solutions. All rights reserved.</div>

</div>
</body>
</html>
```